Business Card Design Can you design a business card design? Looking for something unique and differe

Can you design a business card design? Looking for something unique and different. Can you design a business card design? Looking for something unique and different.Can you design a business card design? Looking for something unique and different.Can you design a business card design? Looking for something unique and different.Can you design a business card design? Looking for something unique and different.Can you design a business card design? Looking for something unique and different.

Industry/Entity Type

Business

Contact Information for Business Card

Can you design a business card design? Looking for something unique and different.

Font styles to use
Serif

```html
<!DOCTYPE html>
<html lang="en">
<head>
<meta charset="utf-8">
<title>Meridian Business Cards</title>
<link rel="stylesheet" href="https://fonts.googleapis.com/css2?family=Lato:wght@400;700&display=swap">
<style>
  :root {
    --backdrop: #3a322e;
    --card: #161616;
    --card-edge: #202020;
    --lilac: #a57fc0;
    --silver: #c9c9c9;
    --grey: #8a8a8a;
    --white: #efefef;
    --rule: #5a5a5a;
  }
  * { box-sizing: border-box; margin: 0; padding: 0; }
  html, body {
    width: 1200px;
    height: 844px;
    overflow: hidden;
    background: var(--backdrop);
    font-family: "Lato", sans-serif;
  }
  .stage {
    position: relative;
    width: 1200px;
    height: 844px;
    display: flex;
    align-items: center;
    justify-content: center;
    gap: 60px;
  }
  .card {
    width: 520px;
    height: 300px;
    background: var(--card);
    border: 1px solid var(--card-edge);
    position: relative;
    box-shadow: 0 18px 40px rgba(0,0,0,.45);
  }
  .card--contact { display: flex; }
  .card__brand {
    width: 54%;
    display: flex;
    flex-direction: column;
    align-items: center;
    justify-content: center;
  }
  .card__details {
    width: 46%;
    padding: 52px 20px 0 22px;
    background: linear-gradient(90deg, #1c1c1c, #181818);
  }
  .brand {
    display: flex;
    align-items: center;
    gap: 10px;
  }
  .brand__mark {
    width: 22px;
    height: 22px;
  }
  .brand__name {
    font-size: 38px;
    font-weight: 700;
    letter-spacing: .5px;
  }
  .brand__tagline {
    display: flex;
    align-items: center;
    gap: 6px;
    margin-top: 2px;
    font-size: 9px;
    letter-spacing: 3px;
    color: var(--grey);
  }
  .brand__tagline::before,
  .brand__tagline::after {
    content: "";
    width: 30px;
    height: 1px;
    background: var(--rule);
  }
  .brand--lilac .brand__name { color: var(--lilac); }
  .brand--lilac .brand__mark { background: var(--lilac); }
  .brand--silver .brand__name { color: var(--silver); }
  .brand--silver .brand__mark { background: var(--silver); }

  .person__name {
    font-size: 21px;
    color: var(--lilac);
    line-height: 1.1;
  }
  .person__role {
    font-size: 13px;
    color: var(--grey);
    margin-bottom: 18px;
  }
  .contact { font-size: 14.5px; color: var(--white); line-height: 1.3; }
  .contact__address { margin-bottom: 14px; }
  .contact__line { display: flex; white-space: nowrap; }
  .contact__label { color: var(--lilac); flex: 0 0 20px; }

  .card--logo {
    display: flex;
    flex-direction: column;
    align-items: center;
    justify-content: center;
  }
</style>
</head>
<body>
  <main class="stage">
    <section class="card card--contact" aria-label="Card back with contact details">
      <div class="card__brand">
        <div class="brand brand--lilac">
          <span class="brand__mark"></span>
          <span class="brand__name">Meridian</span>
        </div>
        <div class="brand__tagline">cost advisory</div>
      </div>
      <div class="card__details">
        <p class="person__name">Daniel Hartley</p>
        <p class="person__role">Managing Director</p>
        <div class="contact">
          <p class="contact__address">48 Harbour Lane, Suite 5<br>Westford, 204518.</p>
          <p class="contact__line"><span class="contact__label">T:</span><span>021-555 014 276</span></p>
          <p class="contact__line"><span class="contact__label">E:</span><span>hello@meridianca.com</span></p>
          <p class="contact__line"><span class="contact__label">W:</span><span>www.meridianca.com</span></p>
        </div>
      </div>
    </section>

    <section class="card card--logo" aria-label="Card front with company name">
      <div class="brand brand--silver">
        <span class="brand__mark"></span>
        <span class="brand__name">Meridian</span>
      </div>
      <div class="brand__tagline">cost advisory</div>
    </section>
  </main>
</body>
</html>
```